Business card for a Exhibition booth fabrication company

Hi. My company would like to change our corporate name card. We are an events and Exhibition stand builder company. We would like our corporate name card to resonate what we do. I need someone to create something unique that relates to the industry that I am in. The graphic designer should be creative to incorporate the elements of my industry and try to blend in well in the design of the card. Our aim is to ensure that we are unique and our card can look different from our competitors.
Updates

Target Market(s)

Marketing and events manager from all companies

Contact Information for Business Card

The business card should have the following details:
Name
Job Title
Email
Website

Colors

Designer to choose colors to be used in the design.

Requirements
Must have
• The card must be look something that is relevant to the service that I am providing. My website is: www.velmora-buildworks.com
• You can see my website to get more information on what service that I am doing
Nice to have
• On the back of my card, I would like to have a globe image with the incorporation of my company logo. This is to indicate that my services can be done in any part of the world.

```html
<!DOCTYPE html>
<html lang="en">
<head>
<meta charset="utf-8">
<title>Velmora Buildworks – Business Card</title>
<link rel="stylesheet" href="https://fonts.googleapis.com/css2?family=Roboto:wght@400;500&display=swap">
<style>
  :root {
    --stage: #2b2c2e;
    --card-white: #ffffff;
    --card-grey: #5e5f61;
    --swoosh-grey: #8a8b8d;
    --brand-red: #e41e26;
    --rule-red: #f08a8d;
    --ink: #4a4b4d;
  }
  * { box-sizing: border-box; margin: 0; padding: 0; }
  html, body { width: 1200px; height: 900px; overflow: hidden; }
  body {
    background: var(--stage);
    font-family: "Roboto", Arial, sans-serif;
    display: flex;
    flex-direction: column;
    align-items: center;
    justify-content: center;
    gap: 40px;
  }
  .card {
    position: relative;
    width: 700px;
    height: 400px;
    border-radius: 22px;
    overflow: hidden;
  }
  .card-front { background: var(--card-white); }
  .card-back {
    background: var(--card-grey);
    display: flex;
    align-items: center;
    justify-content: center;
    gap: 18px;
  }
  .front-waves { position: absolute; inset: 0; }
  .brand-name {
    position: absolute;
    left: 44px;
    top: 104px;
    font-size: 22px;
    font-weight: 500;
    letter-spacing: 4px;
    color: var(--ink);
    text-transform: uppercase;
  }
  .brand-dot {
    position: absolute;
    left: 44px;
    top: 70px;
    width: 22px;
    height: 22px;
    border-radius: 50%;
    background: var(--brand-red);
  }
  .divider {
    position: absolute;
    left: 44px;
    top: 228px;
    width: 606px;
    height: 1.5px;
    background: var(--rule-red);
  }
  .holder {
    position: absolute;
    right: 50px;
    top: 160px;
    text-align: right;
  }
  .holder-name {
    font-size: 30px;
    font-weight: 400;
    letter-spacing: 1px;
    color: var(--brand-red);
    text-transform: uppercase;
    line-height: 1.1;
  }
  .holder-title {
    font-size: 19px;
    color: var(--ink);
    margin-top: 2px;
  }
  .contacts {
    position: absolute;
    left: 44px;
    top: 248px;
    list-style: none;
    font-size: 17px;
    color: var(--ink);
    line-height: 25px;
  }
  .contacts li { display: flex; align-items: center; gap: 10px; }
  .contacts svg { width: 13px; height: 13px; flex: none; }
  .address {
    position: absolute;
    right: 50px;
    top: 252px;
    text-align: right;
    font-size: 18px;
    color: var(--ink);
    line-height: 26px;
  }
  .back-dot {
    width: 34px;
    height: 34px;
    border-radius: 50%;
    background: var(--brand-red);
  }
  .back-name {
    font-size: 34px;
    font-weight: 500;
    letter-spacing: 6px;
    color: #f2f2f2;
    text-transform: uppercase;
  }
</style>
</head>
<body>

<section class="card card-front">
  <svg class="front-waves" viewBox="0 0 700 400" aria-hidden="true">
    <path d="M170,0 C320,0 370,95 480,128 C570,154 640,150 700,150 L700,0 Z" fill="var(--card-grey)"/>
    <path d="M170,0 C320,0 370,95 480,128 C570,154 640,150 700,150 L700,168 C636,168 566,172 474,146 C360,112 300,20 150,20 Z" fill="var(--brand-red)"/>
    <path d="M150,20 C300,20 360,112 474,146 C566,172 636,168 700,168" fill="none" stroke="#ffffff" stroke-width="3"/>
    <path d="M110,38 C230,30 300,80 360,118 C320,92 250,55 160,52 Z" fill="var(--swoosh-grey)"/>
  </svg>

  <span class="brand-dot"></span>
  <div class="brand-name">Velmora Buildworks</div>

  <div class="holder">
    <div class="holder-name">Daniel Hart</div>
    <div class="holder-title">Director</div>
  </div>

  <div class="divider"></div>

  <ul class="contacts">
    <li><svg viewBox="0 0 16 16"><path d="M4 1 L6.5 4.5 L5 6.5 C6 8.5 7.5 10 9.5 11 L11.5 9.5 L15 12 L13 15 C7 14 2 9 1 3 Z" fill="var(--brand-red)"/></svg>+65 81246730</li>
    <li><svg viewBox="0 0 16 16"><rect x="4" y="1" width="8" height="14" rx="1.5" fill="none" stroke="var(--brand-red)" stroke-width="2"/></svg>+974 55082914</li>
    <li><svg viewBox="0 0 16 16"><rect x="1" y="3" width="14" height="10" rx="1" fill="none" stroke="var(--brand-red)" stroke-width="2"/><path d="M1 4 L8 9 L15 4" fill="none" stroke="var(--brand-red)" stroke-width="1.6"/></svg>info@velmora-buildworks.com</li>
    <li><svg viewBox="0 0 16 16"><circle cx="8" cy="8" r="6.5" fill="none" stroke="var(--brand-red)" stroke-width="2"/><path d="M1.5 8 H14.5 M8 1.5 C5 5 5 11 8 14.5 C11 11 11 5 8 1.5" fill="none" stroke="var(--brand-red)" stroke-width="1.2"/></svg>www.velmora-buildworks.com</li>
  </ul>

  <address class="address" style="font-style:normal">
    P.O. Box 4120 Marina Road<br>Lusail - Qatar
  </address>
</section>

<section class="card card-back">
  <span class="back-dot"></span>
  <div class="back-name">Velmora Buildworks</div>
</section>

</body>
</html>
```